Webdesign für Kleingruppenreisen in die Südsteiermark
Zielgruppe
Wir sind ein Start-Up Unternehmen, das als Kleingruppenreisen in die Südsteiermark veranstaltet; der Schwerpunkt liegt auf dem Kulinarischen. Zielgruppe sind Geschäftsleute, die diese Kurzreisen (Do-So) für Marketingzwecke oder als Mitarbeiterbonus (oder auch privat) nutzen möchten.
Aufgabenstellung
Die Homepage soll eine Online-Shop Möglichkeit bieten, in der die Reise (bisher gibt es nur einen Ablauf) gebucht werden kann. Optisch sollte sie sich an das bereits von Ihnen erstellte Logo anlehnen und möglichst ansprechende Fotos von der Südsteiermark, Graz, Leoben usw. enthalten. (Siehe die beiden Flyer und das Logo)
Wir haben inzwischen Bildfreigaben von Haldauer und dem Tourismusverband Kellwinden erhalten und können auch eigene Bilder zur Verfügung stellen. Bitte kontaktieren Sie uns dafür, wenn nötig.

```html
<!DOCTYPE html>
<html lang="de">
<head>
<meta charset="utf-8">
<title>GenussPfade – Reisen für Feinschmecker in die Steiermark</title>
<link rel="stylesheet" href="https://fonts.googleapis.com/css2?family=Kaushan+Script&family=Open+Sans:ital,wght@0,300;0,400;0,600;1,400;1,600&display=swap">
<style>
:root{
  --green:#5e7a36;
  --green-dark:#4f6a2c;
  --green-soft:rgba(94,122,54,.82);
  --grey-bg:#ececec;
  --text:#333;
  --white:#fff;
}
*{box-sizing:border-box;margin:0;padding:0}
html,body{width:1200px;height:2456px;overflow:hidden;background:var(--white)}
body{position:relative;font-family:"Open Sans",Arial,sans-serif;color:var(--text)}
.abs{position:absolute}
.photo{position:absolute}

/* hero */
.hero{left:0;top:0;width:1200px;height:438px;background:linear-gradient(160deg,#4d6a2a 0%,#7f9a46 35%,#c9cfb8 55%,#8aa04c 75%,#56722c 100%);border-top:2px solid var(--green)}
.logo-box{left:225px;top:2px;width:244px;height:143px;background:var(--white);display:flex;align-items:center;justify-content:center;gap:8px}
.logo-box .mark{width:14px;height:14px;border-radius:50%;background:var(--green)}
.logo-box .name{font-family:"Open Sans",sans-serif;font-weight:600;font-size:24px;color:var(--green)}
.main-nav{left:469px;top:88px;width:541px;height:36px;background:var(--green);display:flex;align-items:center;padding-left:86px;gap:15px}
.main-nav a{color:var(--white);text-decoration:none;font-size:12px;font-weight:600;white-space:nowrap}
.hero-caption{left:225px;height:49px;background:var(--green-soft);color:var(--white);font-size:23px;padding:0 10px;display:flex;align-items:center;white-space:nowrap}
.hero-caption.one{top:269px}
.hero-caption.two{top:332px;width:375px}
.slider-dots{left:572px;top:423px;display:flex;gap:14px}
.slider-dots span{width:8px;height:8px;background:rgba(255,255,255,.6)}

/* sections */
.section-title{font-family:"Kaushan Script",cursive;font-weight:400;color:var(--green);text-align:center;width:1200px;left:0;white-space:nowrap}
.divider{left:540px;width:120px;height:20px}
.intro{left:0;top:438px;width:1200px;height:288px;background:var(--grey-bg)}
.body-copy{width:1200px;left:0;text-align:center;font-size:11.5px;line-height:13.5px;color:var(--text)}
.btn{background:var(--green);color:var(--white);font-size:15px;display:flex;align-items:center;justify-content:center;text-decoration:none;white-space:nowrap}

.feature-card{left:403px;top:1124px;width:400px;height:199px;background:linear-gradient(180deg,#7a9a56,#66843f);color:var(--white);text-align:center}
.feature-card h3{font-weight:400;font-size:22px;margin-top:18px}
.feature-card p{font-size:11px;line-height:13.5px;padding:0 24px;margin-top:8px}
.feature-card .outline-btn{position:absolute;left:128px;top:151px;width:137px;height:28px;border:1px solid var(--white);font-size:11px;display:flex;align-items:center;justify-content:center}

.trip-photo{top:1450px;width:220px;height:157px;border:1px solid #ccc}

/* call to action band */
.cta-band{left:0;top:1776px;width:1200px;height:294px;background:linear-gradient(135deg,#6e8a48,#85a05e 50%,#6c8745);color:var(--white)}
.cta-band h2{position:absolute;left:229px;top:40px;font-style:italic;font-weight:600;font-size:30px;line-height:36px;white-space:nowrap}
.cta-band p{position:absolute;left:229px;top:150px;font-weight:300;font-size:22px;line-height:27px;white-space:nowrap}
.cta-band .outline-btn{position:absolute;left:693px;top:193px;width:287px;height:43px;border:1px solid var(--white);font-style:italic;font-weight:600;font-size:23px;display:flex;align-items:center;justify-content:center}

/* footer */
.footer-landscape{left:0;top:2131px;width:560px;height:120px;background:linear-gradient(180deg,rgba(94,122,54,.15),rgba(94,122,54,.85))}
.site-footer{left:0;top:2251px;width:1200px;height:205px;background:var(--green);color:var(--white)}
.contact{position:absolute;left:248px;top:32px;font-size:11px;line-height:13.5px}
.contact .brand{font-weight:600;font-size:12px}
.contact svg{position:absolute;left:-22px}
.footer-menu{position:absolute;top:34px;font-size:11px;line-height:22px}
.footer-menu h4{font-size:11px;font-weight:600;line-height:14px;margin-bottom:4px}
.socials{position:absolute;left:737px;top:42px;display:flex;gap:13px}
.socials span{width:50px;height:50px;border-radius:50%;background:var(--white)}
.footer-rule{position:absolute;left:225px;top:155px;width:750px;height:1px;background:rgba(255,255,255,.6)}
.copyright{position:absolute;left:0;top:168px;width:1200px;text-align:center;font-size:11px}
</style>
</head>
<body>

<header class="abs hero" role="img" aria-label="Weinberge der Südsteiermark mit Trauben im Vordergrund"></header>
<div class="abs logo-box"><span class="mark"></span><span class="name">GenussPfade</span></div>
<nav class="abs main-nav">
  <a href="#">Startseite</a><a href="#">Jetzt buchen</a><a href="#">Shop</a><a href="#">Kontakt</a><a href="#">Ein Menüpunkt</a>
</nav>
<div class="abs hero-caption one">Lorem Ipsum dolor</div>
<div class="abs hero-caption two">consetetur sadipscing elitr, sed</div>
<div class="abs slider-dots"><span></span><span></span><span></span></div>

<section class="abs intro"></section>
<h2 class="abs section-title" style="top:466px;font-size:36px">Haben Sie Geschmack an Besonderem?</h2>
<svg class="abs divider" style="top:519px" viewBox="0 0 120 20"><line x1="0" y1="10" x2="48" y2="10" stroke="#5e7a36"/><circle cx="60" cy="10" r="6" fill="#5e7a36"/><line x1="72" y1="10" x2="120" y2="10" stroke="#5e7a36"/></svg>
<p class="abs body-copy" style="top:558px">Wir lieben die Steiermark mit ihrem guten Essen, hervorragendem Bier und exquisitem Wein und möchten gerne anspruchsvolle Gäste<br>verwöhnen. Als Start-up Unternehmen mit Sitz in Berlin und wollen wir unsere Begeisterung für die Steiermark mit ihren kulinarischen<br>Spezialitäten, wunderschönen Landschaften und gastfreundlichen Menschen gern mit unseren Gästen teilen.<br>„GenussPfade“ ist daher auf der Suche nach Partnern, die mit uns unser neues Projekt in der Steiermark starten möchten.</p>
<a class="abs btn" href="#" style="left:529px;top:647px;width:138px;height:37px">mehr Erfahren</a>

<h2 class="abs section-title" style="top:748px;font-size:36px">Unsere Angebote</h2>
<svg class="abs divider" style="top:801px" viewBox="0 0 120 20"><line x1="0" y1="10" x2="48" y2="10" stroke="#5e7a36"/><circle cx="60" cy="10" r="6" fill="#5e7a36"/><line x1="72" y1="10" x2="120" y2="10" stroke="#5e7a36"/></svg>
<p class="abs body-copy" style="top:839px">Unser Ziel ist es, exklusive Klein-gruppenreisen mit kulinarischem Schwerpunkt in die Steiermark zu führen. Wir konzentrieren uns auf<br>Geschäftsleute aus Berlin und Brandenburg, die unsere Reisen als Marketinginstrument für Kunden, im Rahmen der Wertschätzung von<br>Mitarbeitern oder auch einfach nur privat nutzen möchten.</p>

<div class="photo" style="left:0;top:913px;width:180px;height:200px;background:linear-gradient(180deg,#d8d6cc,#6b6253)" role="img" aria-label="Braukessel im Museum"></div>
<div class="photo" style="left:191px;top:913px;width:200px;height:200px;background:linear-gradient(180deg,#3a7fd0,#6aa0d8 60%,#9a5a3a)" role="img" aria-label="Klapotetz vor blauem Himmel"></div>
<div class="photo" style="left:403px;top:913px;width:200px;height:200px;background:linear-gradient(180deg,#6aa6e0,#c8563a 50%,#d8b070)" role="img" aria-label="Altstadthäuser in Graz mit Uhrturm"></div>
<div class="photo" style="left:616px;top:913px;width:200px;height:200px;background:linear-gradient(135deg,#5c9ce0,#e0b050 55%,#2e3a22)" role="img" aria-label="Gelber Kirchturm"></div>
<div class="photo" style="left:825px;top:913px;width:201px;height:200px;background:linear-gradient(160deg,#3b3a4e,#5a5f78 50%,#5c7a30)" role="img" aria-label="Dunkle Weintrauben"></div>
<div class="photo" style="left:1038px;top:913px;width:162px;height:200px;background:linear-gradient(180deg,#5d8fd0,#d0dce8 50%,#5a8a2a)" role="img" aria-label="Almwiese mit See"></div>
<div class="photo" style="left:0;top:1124px;width:391px;height:199px;background:linear-gradient(180deg,#9aa8b8,#d0d4d8 30%,#4e6a30 60%,#6a8a36)" role="img" aria-label="Wanderer vor Felsmassiv auf der Alm"></div>
<div class="abs feature-card">
  <h3>VII. eine Bildbeschreibung?</h3>
  <p>Lorem ipsum dolor sit amet, consetetur sadipscing elitr, sed diam nonumy eirmod tempor invidunt ut labore et dolore magna aliquyam erat, sed diam voluptua.</p>
  <span class="outline-btn">Jetzt mehr erfahren</span>
</div>
<div class="photo" style="left:828px;top:1124px;width:372px;height:199px;background:linear-gradient(180deg,#e0b888,#f0d09a 35%,#5a7a30 70%,#3e5a22)" role="img" aria-label="Klapotetz im Weinberg bei Sonnenuntergang"></div>

<h2 class="abs section-title" style="top:1355px;font-size:36px">GenussPfade Südsteiermark</h2>
<svg class="abs divider" style="top:1409px" viewBox="0 0 120 20"><line x1="0" y1="10" x2="48" y2="10" stroke="#5e7a36"/><circle cx="60" cy="10" r="6" fill="#5e7a36"/><line x1="72" y1="10" x2="120" y2="10" stroke="#5e7a36"/></svg>
<div class="photo trip-photo" style="left:224px;background:linear-gradient(180deg,#6c9ee0,#8aa0a8 35%,#4e6a2a 65%,#6a7a3a)" role="img" aria-label="Weinberg mit Hügellandschaft"></div>
<div class="photo trip-photo" style="left:490px;background:linear-gradient(180deg,#6a9ee0,#e8eef4 30%,#8a7a3a 60%,#5a6a2e)" role="img" aria-label="Gebirgslandschaft mit Bergseen"></div>
<div class="photo trip-photo" style="left:756px;background:linear-gradient(180deg,#5a8a3a,#a8b0a0 30%,#4a8eb0 55%,#c8c4b8)" role="img" aria-label="Klarer Bergsee mit Felswänden"></div>
<p class="abs body-copy" style="top:1630px">Lernen Sie Leoben, die Hauptstadt des Haldauer-Bieres kennen&nbsp; und erfahren Sie im Haldauer-Museum die Geschichte dieses weltbekannten Gebräus.<br>Entdecken Sie Graz, die ab-wechslungsreiche Landeshauptstadt und Kulturhauptstadt 2003,<br>mit ihren vielfältigen kulturellen Angeboten, den charmanten Gassen und atem-beraubenden&nbsp; Ausblicken.<br>Genießen Sie die südlichere Sonne und kosten Sie die ausgezeichneten Weine der Winzer in der Buschenschank.</p>
<a class="abs btn" href="#" style="left:481px;top:1699px;width:238px;height:37px">GenussPfade jetzt angfragen</a>

<section class="abs cta-band" role="img" aria-label="Weintrauben am Rebstock in Grün getönt">
  <h2>Erleben Sie die<br>gastronomische Vielfalt der Süd-Steiermark</h2>
  <p>Sie suchen ein bestimmtes Gaumenerlebnis?<br>Dann helfen wir Ihnen gerne weiter.</p>
  <span class="outline-btn">Jetzt beraten lassen</span>
</section>

<div class="abs footer-landscape" role="img" aria-label="Grüne Silhouette von Bergen und Altstadt"></div>
<footer class="abs site-footer">
  <div class="contact">
    <svg style="top:0" width="12" height="14" viewBox="0 0 12 14"><path d="M6 0a5 5 0 0 0-5 5c0 4 5 9 5 9s5-5 5-9a5 5 0 0 0-5-5zm0 7a2 2 0 1 1 0-4 2 2 0 0 1 0 4z" fill="#fff"/></svg>
    <div class="brand">GenussPfade</div>
    Marlene Obermaier<br>Lindenweg 12<br>D - 10115 Berlin<br><br>
    <svg style="top:75px" width="14" height="14" viewBox="0 0 14 14"><path d="M3 1l2 3-1.5 1.5a8 8 0 0 0 5 5L10 9l3 2-1 2c-6 0-11-5-11-11z" fill="#fff"/></svg>
    Deutschland: +49 170 0000 123<br>Österreich: +43 681 0000 456
  </div>
  <div class="footer-menu" style="left:460px"><h4>MENÜ</h4>MENÜPUNKT<br>MENÜPUNKT<br>MENÜPUNKT<br>MENÜPUNKT</div>
  <div class="footer-menu" style="left:599px"><h4>MENÜ</h4>MENÜPUNKT<br>MENÜPUNKT<br>MENÜPUNKT<br>MENÜPUNKT</div>
  <div class="socials"><span></span><span></span><span></span><span></span></div>
  <div class="footer-rule"></div>
  <div class="copyright">© 2017. Agentur Krandel</div>
</footer>

</body>
</html>
```